Spring Detox sale graphics for social media

You MUST read the Brief in the WORD document and follow the instructions there. I want to create 10 social media graphics (new Instagram size 4:5 (1080 x 1350 pixels) focusing on our Mother’s Day Spring Detox Sale graphics, using any of the pics attached. Use the attached pics, NO RANDOM STOCK PHOTOGRAPHY. For the color scheme of the graphics, they should all be complementary to the product colors or feel like Spring time.

Target Market(s)

primarily women

Requirements
Must have
• the photos and text attached

```html
<!DOCTYPE html>
<html lang="en">
<head>
<meta charset="utf-8">
<title>Mother's Day Spring Detox Sale – Social Set</title>
<link href="https://fonts.googleapis.com/css2?family=Anton&family=Archivo+Black&family=Kaushan+Script&family=Permanent+Marker&family=Poppins:ital,wght@0,600;0,700;1,800&display=swap" rel="stylesheet">
<style>
  :root{
    --plum:#8d1f57;
    --plum-deep:#74204c;
    --pink:#f3a9d2;
    --pink-mid:#d65ea4;
    --pink-pale:#fdeef7;
    --green:#2d5a4c;
    --green-deep:#0d4a2f;
    --white:#ffffff;
    --photo-light:#f1e4ec;
    --photo-mid:#d9c3cf;
  }
  *{margin:0;padding:0;box-sizing:border-box}
  html,body{width:1200px;height:608px;overflow:hidden;background:var(--white)}
  .sheet{position:relative;width:1200px;height:608px}
  .post{position:absolute;width:232px;height:289px;overflow:hidden;background:var(--plum)}
  .post--pale{background:var(--pink-pale)}
  .post--white{background:var(--white)}
  .post--glow{background:radial-gradient(ellipse at 50% 40%,#a53a72 0%,var(--plum) 70%)}
  .c1{left:12px}.c2{left:249px}.c3{left:484px}.c4{left:720px}.c5{left:957px}
  .r1{top:12px}.r2{top:306px}
  .line{position:absolute;left:0;width:100%;text-align:center;line-height:1;white-space:nowrap}
  .anton{font-family:'Anton',sans-serif}
  .script{font-family:'Kaushan Script',cursive}
  .block{font-family:'Archivo Black',sans-serif}
  .brush{font-family:'Permanent Marker',cursive}
  .italic{font-family:'Poppins',sans-serif;font-style:italic;font-weight:800;letter-spacing:-1px}
  .sans{font-family:'Poppins',sans-serif;font-weight:600}
  .spaced{font-family:'Poppins',sans-serif;font-weight:700;letter-spacing:4px}
  .white{color:var(--white)} .pink{color:var(--pink)} .pinkmid{color:var(--pink-mid)}
  .plum{color:var(--plum)} .green{color:var(--green)} .greendeep{color:var(--green-deep)}
  .photo{position:absolute;background:linear-gradient(180deg,var(--photo-light),var(--photo-mid))}
  .photo--base{background:linear-gradient(180deg,#fbf4f8 0%,#ffffff 100%)}
  .tag{position:absolute;left:22px;top:16px;width:92px;height:28px;background:var(--green);
       clip-path:polygon(0 0,88% 0,100% 50%,88% 100%,0 100%);color:var(--white);
       font-family:'Anton',sans-serif;font-size:22px;line-height:28px;padding-left:6px}
  .card{position:absolute;left:24px;top:144px;width:186px;height:124px;border-radius:6px;
        background:linear-gradient(135deg,#fbe3ef,#f3c6de)}
  .boxed{position:absolute;left:20px;width:192px;height:28px;background:var(--white);
         color:var(--plum);font-family:'Anton',sans-serif;font-size:24px;line-height:28px;text-align:center}
  .pill{position:absolute;left:38px;top:144px;width:156px;height:38px;border-radius:8px;background:var(--white);
        color:var(--plum);font-family:'Poppins',sans-serif;font-style:italic;font-weight:800;font-size:12.5px;
        line-height:17px;text-align:center;padding-top:2px;letter-spacing:-.4px}
  .band{position:absolute;left:24px;top:192px;width:186px;height:30px;background:var(--pink)}
</style>
</head>
<body>
<main class="sheet">

  <!-- 1 -->
  <section class="post post--glow c1 r1">
    <p class="line script white" style="top:22px;font-size:29px">Mother's Day</p>
    <p class="line anton pink" style="top:52px;font-size:64px">SPRING</p>
    <p class="line anton white" style="top:122px;font-size:42px">DETOX SALE</p>
    <p class="line sans pink" style="top:168px;font-size:16px">25% Off Everything!</p>
    <div class="photo photo--base" style="left:0;top:200px;width:232px;height:89px;border-radius:50% 50% 0 0/20px 20px 0 0" role="img" aria-label="Four supplement bottles in a row"></div>
  </section>

  <!-- 2 -->
  <section class="post post--pale c2 r1">
    <div class="tag">25% OFF</div>
    <div class="photo" style="left:122px;top:12px;width:86px;height:34px;border-radius:4px" role="img" aria-label="Four small supplement bottles"></div>
    <p class="line anton plum" style="top:48px;font-size:68px">SPRING</p>
    <p class="line script green" style="top:118px;font-size:36px">Detox Sale</p>
    <p class="line anton pinkmid" style="top:154px;font-size:42px">THIS SPRING</p>
    <p class="line script green" style="top:196px;font-size:36px">Shine This</p>
    <p class="line anton plum" style="top:230px;font-size:52px">SUMMER</p>
  </section>

  <!-- 3 -->
  <section class="post c3 r1">
    <p class="line anton white" style="top:26px;font-size:54px">25% OFF</p>
    <p class="line script white" style="top:92px;font-size:33px">Mother's Day</p>
    <div class="card"></div>
    <p class="line script green" style="top:152px;left:30px;width:100px;font-size:26px">Spring</p>
    <p class="line anton green" style="top:180px;left:30px;width:100px;font-size:36px">DETOX</p>
    <p class="line anton pinkmid" style="top:218px;left:30px;width:100px;font-size:42px">SALE</p>
    <div class="photo" style="left:132px;top:140px;width:82px;height:142px;border-radius:10px 10px 4px 4px" role="img" aria-label="Supplement bottle"></div>
  </section>

  <!-- 4 -->
  <section class="post post--pale c4 r1">
    <p class="line block green" style="top:30px;font-size:31px">25% OFF</p>
    <p class="line anton green" style="top:64px;font-size:30px">ALL SUPPLEMENTS</p>
    <p class="line anton green" style="top:96px;font-size:46px">SPRING</p>
    <p class="line block pinkmid" style="top:140px;font-size:43px">DETOX</p>
    <p class="line anton greendeep" style="top:178px;font-size:96px">SALE</p>
  </section>

  <!-- 5 -->
  <section class="post post--glow c5 r1">
    <p class="line anton" style="top:28px;left:32px;width:auto;font-size:104px;background:linear-gradient(180deg,#f6a3d6,#ffffff);-webkit-background-clip:text;background-clip:text;color:transparent">25</p>
    <p class="line anton pink" style="top:30px;left:148px;width:auto;font-size:54px">%</p>
    <p class="line anton white" style="top:90px;left:148px;width:auto;font-size:46px">OFF</p>
    <p class="line script pink" style="top:140px;font-size:44px">Mother's</p>
    <p class="line spaced white" style="top:186px;font-size:13px">DAY SALE</p>
    <p class="line script pink" style="top:206px;font-size:44px">Refresh</p>
    <p class="line spaced white" style="top:262px;font-size:13px">YOUR BODY</p>
  </section>

  <!-- 6 -->
  <section class="post post--white c1 r2">
    <p class="line anton green" style="top:16px;font-size:52px">25% OFF</p>
    <p class="line script plum" style="top:72px;font-size:30px">Mother's Day</p>
    <p class="line anton greendeep" style="top:96px;font-size:104px">SALE</p>
    <div class="photo" style="left:150px;top:150px;width:82px;height:139px;border-radius:40px 40px 0 0" role="img" aria-label="Smiling woman presenting supplement bottles"></div>
    <p class="line script pinkmid" style="top:202px;left:12px;width:auto;font-size:48px">Feel</p>
    <p class="line anton green" style="top:262px;left:12px;width:auto;font-size:20px">AMAZING AGAIN</p>
  </section>

  <!-- 7 -->
  <section class="post c2 r2">
    <p class="line anton white" style="top:28px;font-size:50px">25% OFF</p>
    <p class="line script white" style="top:84px;font-size:21px">Mother's Day Sale</p>
    <div class="boxed" style="top:112px">SPRING DETOX FOR A</div>
    <p class="line anton pink" style="top:144px;font-size:56px">SUMMER</p>
    <p class="line brush white" style="top:200px;font-size:64px">BODY</p>
  </section>

  <!-- 8 -->
  <section class="post c3 r2">
    <p class="line italic white" style="top:18px;font-size:34px">25% Off</p>
    <p class="line script white" style="top:54px;font-size:48px">Mother's</p>
    <p class="line italic white" style="top:100px;font-size:33px">Day Sale</p>
    <div class="pill">Detox this Summer<br>Shine this Summer</div>
    <div class="photo photo--base" style="left:0;top:200px;width:232px;height:89px;border-radius:50% 50% 0 0/18px 18px 0 0" role="img" aria-label="Four supplement bottles in a row"></div>
  </section>

  <!-- 9 -->
  <section class="post c4 r2">
    <p class="line anton" style="top:30px;left:20px;width:auto;font-size:112px;color:#ece2e7" role="img" aria-label="Numerals filled with a supplement bottle photo">25</p>
    <p class="line anton white" style="top:34px;left:146px;width:auto;font-size:56px">%</p>
    <p class="line anton pink" style="top:98px;left:146px;width:auto;font-size:46px">OFF</p>
    <p class="line anton white" style="top:150px;font-size:40px">EVERYTHING</p>
    <div class="band"></div>
    <p class="line script plum" style="top:192px;font-size:25px">Mother's Day</p>
    <p class="line anton white" style="top:228px;font-size:26px">SPRING DETOX SALE</p>
  </section>

  <!-- 10 -->
  <section class="post c5 r2">
    <p class="line italic white" style="top:18px;font-size:26px">25% OFF</p>
    <p class="line brush white" style="top:46px;font-size:48px">SPRING</p>
    <p class="line italic white" style="top:100px;font-size:25px">Detox Sale</p>
    <div class="photo" style="left:38px;top:134px;width:156px;height:88px;border-radius:8px" role="img" aria-label="Four supplement bottles grouped together"></div>
    <p class="line italic white" style="top:228px;font-size:23px">Spring Reset.</p>
    <p class="line italic white" style="top:254px;font-size:23px">Summer Ready</p>
  </section>

</main>
</body>
</html>
```